Business Card Design

Online clothing womens clothing store, I sell my clothing online and at the markets.

i would like the attached picture on the front of the card and the contact information on the back.

Industry/Entity Type

Business

Contact Information for Business Card

Marlow Thread
Karen Whitfield
(Instagram symbol) _marlow_thread_
(Facebook symbol) www.fakebookexample.com/marlowthreadau/

W : www.marlowthread.example.au
E : info@marlowthread.example.au
P : 0498716204

```html
<!DOCTYPE html>
<html lang="en">
<head>
<meta charset="utf-8">
<title>Marlow Thread – Business Card</title>
<link rel="stylesheet" href="https://fonts.googleapis.com/css2?family=Josefin+Sans:wght@300&family=Oswald:wght@500&family=Cinzel:wght@400&family=Arimo:wght@400&display=swap">
<style>
  :root {
    --canvas-bg: #e9e6e1;
    --card-black: #0b0b0b;
    --card-black-sheen: #262626;
    --ink-white: #ffffff;
    --ink-dark: #0b0b0b;
    --photo-light: #e4e4e4;
    --photo-mid: #b9b9b9;
    --photo-dark: #5c5c5c;
  }
  * { box-sizing: border-box; margin: 0; padding: 0; }
  html, body { width: 1200px; height: 892px; overflow: hidden; }
  body { background: var(--canvas-bg); position: relative; }

  .card {
    position: absolute;
    width: 620px;
    height: 354px;
    left: 290px;
    overflow: hidden;
    box-shadow: 0 10px 28px rgba(0,0,0,.22);
  }

  /* Front */
  .card-front { top: 52px; background: var(--photo-light); }
  .front-photo {
    position: absolute; inset: 0;
    background:
      radial-gradient(ellipse 55% 70% at 72% 62%, var(--photo-dark) 0%, var(--photo-mid) 55%, transparent 80%),
      linear-gradient(160deg, var(--photo-light) 0%, #d2d2d2 60%, var(--photo-mid) 100%);
  }
  .front-brand {
    position: absolute;
    left: 150px; top: 196px;
    font-family: "Oswald", sans-serif;
    font-weight: 500;
    font-size: 58px;
    line-height: 1;
    letter-spacing: 3px;
    color: var(--ink-white);
    text-transform: uppercase;
    white-space: nowrap;
  }

  /* Back */
  .card-back {
    top: 486px;
    background: linear-gradient(120deg, var(--card-black) 0%, var(--card-black-sheen) 38%, var(--card-black) 62%);
    color: var(--ink-white);
  }
  .back-brand {
    position: absolute;
    left: 24px; top: 30px;
    font-family: "Josefin Sans", sans-serif;
    font-weight: 300;
    font-size: 21px;
    letter-spacing: 6px;
    text-transform: uppercase;
    white-space: nowrap;
  }
  .divider {
    position: absolute;
    left: 334px; top: 24px;
    width: 1.5px; height: 306px;
    background: var(--ink-white);
  }
  .holder-name {
    position: absolute;
    left: 352px; top: 124px;
    font-family: "Cinzel", serif;
    font-size: 21px;
    letter-spacing: 3px;
    white-space: nowrap;
  }
  .contact-list {
    position: absolute;
    left: 350px; top: 172px;
    list-style: none;
    font-family: "Arimo", sans-serif;
    font-size: 14px;
    line-height: 26px;
  }
  .contact-list li { display: flex; align-items: center; white-space: nowrap; }
  .contact-icon {
    width: 14px; height: 14px;
    margin-right: 9px;
    background: var(--ink-white);
    flex: none;
  }
</style>
</head>
<body>
  <section class="card card-front" aria-label="Card front">
    <div class="front-photo" role="img" aria-label="Black and white photograph of a woman half hidden in drifting grey smoke"></div>
    <div class="front-brand">Marlow Thread</div>
  </section>

  <section class="card card-back" aria-label="Card back">
    <div class="back-brand">Marlow Thread</div>
    <div class="divider"></div>
    <div class="holder-name">Karen Whitfield</div>
    <ul class="contact-list">
      <li>
        <svg class="contact-icon" viewBox="0 0 16 16" aria-hidden="true">
          <path d="M4 3.5h2l1 2.5-1.3 1a7 7 0 0 0 3.3 3.3l1-1.3 2.5 1v2a1 1 0 0 1-1 1A9 9 0 0 1 3 4.5a1 1 0 0 1 1-1z" fill="#0b0b0b"/>
        </svg>0498716204
      </li>
      <li><span class="contact-icon" aria-hidden="true"></span>marlowthreadau</li>
      <li><span class="contact-icon" aria-hidden="true"></span>marlow_thread</li>
      <li><span class="contact-icon" aria-hidden="true"></span>www.marlowthread.example.au</li>
      <li>
        <svg class="contact-icon" viewBox="0 0 16 16" aria-hidden="true">
          <rect x="2.5" y="4.5" width="11" height="7" fill="none" stroke="#0b0b0b" stroke-width="1.2"/>
          <path d="M2.5 4.5l5.5 4 5.5-4" fill="none" stroke="#0b0b0b" stroke-width="1.2"/>
        </svg>info@marlowthread.example.au
      </li>
    </ul>
  </section>
</body>
</html>
```